Business Postcard Design for Personal Training Company

Need a postcard design for my company called "Copperleaf Studio" Colors are Navy Blue, Blue, Grey and White.

On the front I want there to be pictures and it to feature a box that says "Free Consultation + 50% off your first session!"

And somehow to feature the following phrases " Lose Weight. Gain Muscle."
"Customized Personal training using Q-Pulse, the latest technology in fitness. Reach your fitness goals in just two 25-min sessions per week"

Also want featured the following phrases (maybe on back):

"up to 18 times more effective than a conventional gym workout"

I need the back of the postcard to have all my business information:

Address: 287 Wendover Ln, Building D Suite 318, Costa Mesa CA 92631
Website: copperleaf-studio.example
Phone #: (949) 555-0137
E-mail: copperleafwellness@mailbox.example

I am going to upload my logo, before and after pictures and pictures of people training on the device. Feel free to use as many/or little photos as you want.

Target Market(s)

Wealthy Adults 40+ years old looking for a personal trainer

Industry/Entity Type

Personal Trainer

Colors
0455a3
85cae6
aaaaaa
ffffff

Requirements
Must have
• At least two of the before and after photos, and two or more photos of people working out on the device.

```html
<!DOCTYPE html>
<html lang="en">
<head>
<meta charset="utf-8">
<title>Copperleaf Studio Postcard</title>
<link href="https://fonts.googleapis.com/css2?family=Bebas+Neue&family=Raleway:wght@500&family=Gochi+Hand&display=swap" rel="stylesheet">
<style>
  :root {
    --navy: #24307e;
    --navy-deep: #1b2466;
    --blue: #0455a3;
    --cyan: #1ba7dc;
    --sky: #85cae6;
    --mist: #bfe6f4;
    --grey: #aaaaaa;
    --white: #ffffff;
    --ink: #22303d;
  }
  html, body {
    margin: 0;
    padding: 0;
    width: 1200px;
    height: 930px;
    overflow: hidden;
    background: var(--white);
  }
  .postcard {
    position: absolute;
    left: 0;
    top: 0;
    width: 579px;
    height: 765px;
    overflow: hidden;
  }
  .backdrop {
    position: absolute;
    inset: 0;
    width: 579px;
    height: 765px;
  }
  .contact-list {
    position: absolute;
    left: 36px;
    top: 36px;
    margin: 0;
    padding: 0;
    list-style: none;
    font-family: "Bebas Neue", "Oswald", sans-serif;
    font-size: 26px;
    line-height: 31px;
    letter-spacing: 0.3px;
    color: var(--white);
    text-transform: uppercase;
  }
  .contact-item {
    display: flex;
    align-items: flex-start;
    margin-bottom: 8px;
  }
  .contact-icon {
    flex: 0 0 20px;
    width: 20px;
    height: 20px;
    margin: 4px 24px 0 0;
  }
  .intro {
    position: absolute;
    left: 42px;
    top: 334px;
    margin: 0;
    font-family: "Raleway", sans-serif;
    font-weight: 500;
    font-size: 21px;
    line-height: 27px;
    color: var(--white);
    text-shadow: 0 0 6px rgba(10, 40, 90, 0.35);
  }
  .claim {
    position: absolute;
    left: 32px;
    top: 588px;
    margin: 0;
    font-family: "Gochi Hand", cursive;
    font-size: 25px;
    line-height: 30px;
    color: var(--ink);
  }
</style>
</head>
<body>
  <main class="postcard">
    <svg class="backdrop" viewBox="0 0 579 765" xmlns="http://www.w3.org/2000/svg">
      <defs>
        <linearGradient id="studioTone" x1="0" y1="0" x2="1" y2="1">
          <stop offset="0" stop-color="#1d5f9e"/>
          <stop offset="0.55" stop-color="#2a3b8f"/>
          <stop offset="1" stop-color="#1b2466"/>
        </linearGradient>
        <linearGradient id="trainingTone" x1="0" y1="0" x2="1" y2="0">
          <stop offset="0" stop-color="#1583c4"/>
          <stop offset="1" stop-color="#1fb3e3"/>
        </linearGradient>
        <linearGradient id="ballTone" x1="0" y1="0" x2="0" y2="1">
          <stop offset="0" stop-color="#3fb6e6"/>
          <stop offset="1" stop-color="#b7e4f4"/>
        </linearGradient>
        <linearGradient id="trainerTone" x1="0" y1="0" x2="0" y2="1">
          <stop offset="0" stop-color="#f2d9a6" stop-opacity="0.85"/>
          <stop offset="0.35" stop-color="#2b2f3a" stop-opacity="0.85"/>
          <stop offset="0.7" stop-color="#4aa9e0" stop-opacity="0.9"/>
          <stop offset="1" stop-color="#d8eef8" stop-opacity="0.6"/>
        </linearGradient>
      </defs>
      <polygon points="0,0 579,0 579,215 0,282" fill="url(#studioTone)" role="img" aria-label="Photo of a smiling trainer in the studio, tinted navy"/>
      <polygon points="0,282 579,215 579,470 0,528" fill="url(#trainingTone)" role="img" aria-label="Photo of a client training on the Q-Pulse device, tinted blue"/>
      <polygon points="0,528 579,470 579,765 0,765" fill="url(#ballTone)" role="img" aria-label="Photo of a stability ball and dumbbells, tinted light blue"/>
      <rect x="378" y="408" width="170" height="344" rx="70" fill="url(#trainerTone)" role="img" aria-label="Cut-out photo of a trainer holding small dumbbells"/>
    </svg>

    <ul class="contact-list">
      <li class="contact-item">
        <svg class="contact-icon" viewBox="0 0 20 20"><circle cx="10" cy="10" r="9" fill="#8fa6e8"/><circle cx="10" cy="10" r="5.5" fill="none" stroke="#fff" stroke-width="1.4"/><line x1="4.5" y1="10" x2="15.5" y2="10" stroke="#fff" stroke-width="1.2"/><ellipse cx="10" cy="10" rx="2.4" ry="5.5" fill="none" stroke="#fff" stroke-width="1.2"/></svg>
        <span>copperleaf-studio.example</span>
      </li>
      <li class="contact-item">
        <svg class="contact-icon" viewBox="0 0 20 20"><circle cx="10" cy="10" r="9" fill="#8fa6e8"/><path d="M7 5 L9 5 L9.6 8 L8.4 9 Q9.4 11.2 11 12 L12 10.8 L15 11.4 L15 13.4 Q11 15 7.4 11.2 Q5.6 8.6 7 5 Z" fill="#fff"/></svg>
        <span>(949) 555-0137</span>
      </li>
      <li class="contact-item">
        <svg class="contact-icon" viewBox="0 0 20 20"><circle cx="10" cy="10" r="9" fill="#8fa6e8"/><text x="10" y="14" text-anchor="middle" font-family="Arial, sans-serif" font-size="11" font-weight="700" fill="#fff">@</text></svg>
        <span>copperleafwellness@mailbox.example</span>
      </li>
      <li class="contact-item">
        <svg class="contact-icon" viewBox="0 0 20 20"><circle cx="10" cy="10" r="9" fill="#8fa6e8"/><path d="M10 4.5 L15.5 9.5 L13.8 9.5 L13.8 14.5 L11.2 14.5 L11.2 11.5 L8.8 11.5 L8.8 14.5 L6.2 14.5 L6.2 9.5 L4.5 9.5 Z" fill="#fff"/></svg>
        <span>287 Wendover Ln, Building D Suite 318,<br>Costa Mesa CA 92631</span>
      </li>
    </ul>

    <p class="intro">Customized Personal training using<br>Q-Pulse, the latest technology in fitness.<br>Reach your fitness goals in just two<br>25-min sessions per week</p>

    <p class="claim">up to 18 times more effective than a<br>conventional gym workout</p>
  </main>
</body>
</html>
```